Letterhead for Business Law Firm

We need a letter head for our firm based on the design we have settled on and it is attached. Our clients are small and large businesses around the world, and our letterhead is used typically for formal legal purposes such as demand letters (accusing the recipient of doing bad things) or responding to demand letters. It may also be sent to regulators and other government agencies. So this needs to be tasteful, but a little edgy as well - we try to convey that we are a firm that is different - businesses and investors come to us for creative, quick advice, typically in high stress circumstances, and for our ability to work through high conflict situations, and rapid paced engagements.

Target Market(s)

Lawyers, business executives, investors, government regulators who may receive letters from this firm on behalf of its clients.

Industry/Entity Type

Business

Requirements
Must have
• The design and the firm's contact information:
• Thornwell Law Firm, P.C.
• 1876 NE 57th Ave
• Portland, OR 97213
• phone: 971 555 0147
• fax: 971 555 0182
• in what placement and how depicted (e.g. a phone icon instead of the word "phone") I leave to your creative ideas.
Nice to have
• design and information can be placed at the top, bottom and/or sides of the letter, and the design should be for a standard letter size paper - and can have a separate design for the second page.

```html
<!DOCTYPE html>
<html lang="en">
<head>
<meta charset="utf-8">
<title>Thornwell Law Firm, P.C. — Letterhead</title>
<link rel="stylesheet" href="https://fonts.googleapis.com/css2?family=Ubuntu:wght@400;500&display=swap">
<style>
  :root {
    --paper: #ffffff;
    --ink: #333333;
    --mark-dark: #141014;
    --teal: #2e6e73;
    --rule: #8a8a8a;
    --frame: #9a9a9a;
    --band-edge: #1c1c1e;
  }
  html, body {
    margin: 0;
    padding: 0;
    width: 845px;
    height: 1200px;
    overflow: hidden;
    background: var(--paper);
  }
  .letterhead {
    position: relative;
    width: 845px;
    height: 1200px;
    box-sizing: border-box;
    border: 1px solid var(--frame);
    background: var(--paper);
    font-family: "Ubuntu", sans-serif;
    color: var(--ink);
  }
  .brand {
    position: absolute;
    left: 18px;
    top: 18px;
    height: 66px;
    display: flex;
    align-items: center;
    gap: 14px;
  }
  .brand-square {
    width: 66px;
    height: 66px;
    background: var(--mark-dark);
  }
  .brand-name {
    font-size: 34px;
    font-weight: 400;
    letter-spacing: 8px;
    color: var(--mark-dark);
    line-height: 1;
  }
  .header-rule {
    position: absolute;
    left: 292px;
    top: 84px;
    width: 545px;
    height: 1px;
    background: var(--rule);
  }
  .contact-list {
    position: absolute;
    left: 704px;
    top: 18px;
    margin: 0;
    padding: 0;
    list-style: none;
  }
  .contact-item {
    display: flex;
    align-items: center;
    height: 20px;
    font-size: 12px;
    white-space: nowrap;
  }
  .contact-icon {
    width: 16px;
    height: 16px;
    margin-right: 8px;
    flex: none;
  }
  .street-address {
    position: absolute;
    right: 44px;
    top: 90px;
    margin: 0;
    font-size: 12.5px;
    font-weight: 500;
    white-space: nowrap;
  }
  .footer-band {
    position: absolute;
    left: 0;
    right: 0;
    bottom: 0;
    height: 40px;
    background: linear-gradient(90deg, var(--band-edge) 0%, #5a6366 22%, var(--teal) 50%, #5a6366 78%, var(--band-edge) 100%);
  }
</style>
</head>
<body>
  <main class="letterhead">
    <header>
      <div class="brand">
        <div class="brand-square"></div>
        <span class="brand-name">THORNWELL</span>
      </div>
      <div class="header-rule"></div>

      <ul class="contact-list">
        <li class="contact-item">
          <svg class="contact-icon" viewBox="0 0 16 16" role="img" aria-label="Phone">
            <circle cx="8" cy="8" r="8" fill="#111"/>
            <path d="M5.2 4.4c.5-.4 1-.3 1.2.2l.6 1.4c.1.3 0 .6-.3.8l-.5.4c.4 1 1.2 1.9 2.2 2.4l.5-.5c.2-.3.5-.3.8-.2l1.3.7c.5.2.5.8.1 1.2-.9.9-2.2.8-3.6-.2-1.7-1.2-3-3.2-3-4.6 0-.7.3-1.3.7-1.6z" fill="#fff"/>
          </svg>
          971 555 0147
        </li>
        <li class="contact-item">
          <svg class="contact-icon" viewBox="0 0 16 16" role="img" aria-label="Fax">
            <circle cx="8" cy="8" r="8" fill="#111"/>
            <rect x="5.6" y="3.8" width="4.8" height="2.6" fill="none" stroke="#fff" stroke-width="0.9"/>
            <rect x="4" y="6.4" width="8" height="3.8" rx="0.6" fill="#fff"/>
            <rect x="5.6" y="9" width="4.8" height="3.2" fill="#111" stroke="#fff" stroke-width="0.9"/>
          </svg>
          971 555 0182
        </li>
        <li class="contact-item">
          <svg class="contact-icon" viewBox="0 0 16 16" role="img" aria-label="Website">
            <circle cx="8" cy="8" r="8" fill="#111"/>
            <g fill="none" stroke="#fff" stroke-width="0.9">
              <circle cx="8" cy="8" r="4.6"/>
              <ellipse cx="8" cy="8" rx="2" ry="4.6"/>
              <path d="M3.4 8h9.2M4.2 5.6h7.6M4.2 10.4h7.6"/>
            </g>
          </svg>
          thornwelllaw.com
        </li>
      </ul>

      <p class="street-address">1876 NE 57th Ave, Portland, OR 97213</p>
    </header>

    <footer class="footer-band"></footer>
  </main>
</body>
</html>
```